New B2C website design to help dads be better dads

DadHarbor is a website to help dads be the “best dad you can be.”

We require our website to be designed into a PSD format, no coding necessary.

The general concept is a two-page design. The first page is the login page, the second page is the home page. Once at the home page, rather than navigating to and from different pages, the user will push and pull through different visual and functional layers of the hierarchy. In theory, this should add to the user experience by having a visual anchor of where they are (through layered pagination) as well as improving loading times since the new information should only be a delta in data load versus a brand new page load.

The general look-and-feel we are going for is clean, simple, minimal. This means that the winning design will show us a good eye for web-optimized typography, good use of white (negative) space, and good use of a visually pleasing grid.

We require a total of 6 page "views" plus the landing page. We note that many of the views are similar to one another.
Landing page
Milestone view
Task view
Content view, articles
Content view, products
Search view
What's new view

Please review all of the additional information provided as well as the attachments for examples.

We provide the following websites as good references for:

Typography:
http://example-kelvorn.com/journal/

Use of white space:
http://www.trenvaskit.com/
http://moldrefin.com/

Example for “scrolling” page concept as well as good balance of color, typography, and white space:
http://www.qorbitalmeet.eu/

Please contact us with questions so that we can guide your design effort.
Updates

Hello designers,

The following information is added to help guide the design process:

1.  For the text dialogue below the landing page, please assume the following word count:
"why are we making dad harbor?": 250 words
"who are we?" 200 words
"what's the deal with the penguin logo?" 300 words

For the social media links, please see http://www.gravelplumbs.com/
Notice the floating "social" bar that is always to the right.  This is the concept we are going for, please try to implement this as you see fit. 

Target Market(s)

Fathers of young children ages 0-6 years old.

Industry/Entity Type

Product

Font styles to use
Sans Serif

Requirements
Must have
• Clean lines, minimal design concept

Incorporation of our logo (see attached document)

Header content is static for all views after landing page, see example

This page WILL be responsive, please keep that in mind when designing
The timeline bar should be to the left, with the timeline bar’s “milestones” also being responsive.

Designer is free to suggest font types, but any fonts used must be royalty-free and web-optimized. We request a minimum number of font types as well as fonts that load relatively fast. We reinforce that visually appealing typography is a significant factor in the winning design choice.

While we are not expecting the winning design to include code, please keep in mind that the final implementation needs to be optimized for desktop, tablet, and mobile platforms.

If you are using stock photography that is not generated by you, please provide where/how we can obtain imagery, as well as price.

All custom graphics must be available in original formats; Photoshop/GIMP layered files for layout design, and vector formats for logos, icons and other graphical elements.

Please incorporate “Blue” into design elements as you see fit, as the RGB 67 74 169 Blue is the primary color used in our brand. The complement to this blue is 255 202 0, a brownish orange. Feel free to use this color as well, although please keep it to a lesser amount.

Background color is your choice, do not feel the need to use the grey.
Should not have
• Excessive graphical content such that it affects loading times

Excessive use of too many font types such that it affects loading times

```html
<!DOCTYPE html>
<html lang="en">
<head>
<meta charset="utf-8">
<title>DadHarbor — Prepare for the baby arrival</title>
<link rel="stylesheet" href="https://fonts.googleapis.com/css2?family=Source+Sans+3:wght@400;600&family=Tinos&display=swap">
<style>
  :root {
    --brand-blue: #434aa9;
    --brand-gold: #f0b400;
    --star: #f5a300;
    --header-bg: #f6f6f6;
    --page-bg: #ffffff;
    --text: #3a3a3a;
    --muted: #555555;
    --nav: #666666;
    --footer-bg: #0d0d0d;
    --footer-text: #ffffff;
    --card-shadow: rgba(0,0,0,0.18);
    --btn-top: #5a5a5a;
    --btn-bottom: #2e2e2e;
    --social-a: #3b5a9a;
    --social-b: #2ba5dc;
    --social-c: #f26c1f;
    --social-d: #e02a26;
  }
  * { box-sizing: border-box; margin: 0; padding: 0; }
  html, body { width: 1140px; height: 1200px; overflow: hidden; }
  body {
    position: relative;
    background: var(--page-bg);
    font-family: "Source Sans 3", sans-serif;
    color: var(--text);
  }

  .site-header {
    position: absolute; left: 0; top: 0; width: 1140px; height: 166px;
    background: var(--header-bg);
    box-shadow: 0 1px 4px rgba(0,0,0,0.12);
  }
  .brand {
    position: absolute; left: 82px; top: 104px;
    display: flex; align-items: center; gap: 8px;
    font-family: "Source Sans 3", sans-serif; font-weight: 600;
    font-size: 20px; letter-spacing: 0.5px; color: var(--brand-blue);
  }
  .brand-dot { width: 14px; height: 14px; border-radius: 50%; background: var(--brand-blue); }
  .welcome {
    position: absolute; right: 82px; top: 33px;
    font-family: "Tinos", serif; font-size: 27px; color: var(--brand-blue);
  }
  .score {
    position: absolute; left: 532px; top: 111px;
    font-size: 17px; color: var(--brand-gold);
  }
  .search-btn {
    position: absolute; left: 739px; top: 105px; width: 110px; height: 35px;
    background: linear-gradient(var(--btn-top), var(--btn-bottom));
    border: 1px solid #222; color: #fff; font-family: inherit; font-size: 17px;
    box-shadow: 0 1px 2px rgba(0,0,0,0.3);
  }
  .account-nav {
    position: absolute; left: 885px; top: 111px;
    display: flex; align-items: center; font-size: 16px; color: var(--nav);
  }
  .account-nav span + span {
    margin-left: 16px; padding-left: 18px; border-left: 1px dotted #bbb;
  }

  .section-title {
    position: absolute; left: 82px; top: 203px;
    font-family: "Tinos", serif; font-weight: 400; font-size: 27px; color: var(--brand-blue);
  }

  .checklist {
    position: absolute; left: 84px; top: 255px; width: 251px; height: 364px;
    background: #fff; box-shadow: 0 0 5px var(--card-shadow);
    list-style: none; padding: 27px 0 0 18px;
  }
  .checklist li {
    display: flex; align-items: center; height: 41px;
    font-size: 14.5px; color: var(--text);
  }
  .checklist li::before {
    content: ""; width: 11px; height: 11px; margin-right: 12px;
    border: 1px solid #d6d6d6; background: #f1f1f1;
  }

  .product-card {
    position: absolute; width: 296px; height: 374px;
    background: #fff; box-shadow: 0 0 5px var(--card-shadow);
    padding: 6px;
  }
  .product-photo { width: 284px; height: 174px; }
  .photo-a { background: linear-gradient(135deg, #4a5a3a, #b8b8b8 45%, #6a6a6a); }
  .photo-b { background: linear-gradient(135deg, #d8414e, #e9c7b0 45%, #2c2c2c); }
  .photo-c { background: linear-gradient(135deg, #8f9e7a, #2a2a2a 40%, #4c5d7a); }
  .photo-d { background: linear-gradient(135deg, #9aa590, #3a3a3a 45%, #23262e); }
  .product-title {
    margin: 12px 1px 0; font-family: "Tinos", serif; font-size: 16px; line-height: 23px;
    color: var(--brand-blue);
  }
  .rating {
    display: flex; justify-content: space-between; align-items: center;
    margin: 10px 6px 0 1px;
  }
  .stars { display: flex; gap: 4px; }
  .stars svg { width: 19px; height: 19px; fill: var(--star); }
  .rating-count { font-family: "Tinos", serif; font-size: 16px; color: var(--text); }
  .product-text {
    margin: 12px 1px 0; font-size: 14.5px; line-height: 25px; color: var(--muted);
  }

  .site-footer {
    position: absolute; left: 0; top: 1101px; width: 1140px; height: 99px;
    background: var(--footer-bg); color: var(--footer-text);
  }
  .footer-links { position: absolute; left: 84px; top: 24px; font-size: 13.5px; }
  .copyright { position: absolute; left: 85px; top: 56px; font-size: 13.5px; }
  .social { position: absolute; left: 831px; top: 32px; display: flex; gap: 13px; }
  .social span { width: 34px; height: 34px; display: block; }
</style>
</head>
<body>
  <header class="site-header">
    <div class="brand"><span class="brand-dot"></span>DADHARBOR</div>
    <p class="welcome">Welcome Tomas, What would you like to do today?</p>
    <p class="score">Super Dad Score: 10,500</p>
    <button class="search-btn" type="button">Search</button>
    <nav class="account-nav"><span>MY ACCOUNT</span><span>LOGIN</span></nav>
  </header>

  <h1 class="section-title">Prepare for the baby arrival</h1>

  <ul class="checklist">
    <li>Buy a crib</li>
    <li>Assemble the crib</li>
    <li>Buy a Strlooer</li>
    <li>Buy a carseat</li>
    <li>Install a carseat</li>
    <li>Learn to change a diaper</li>
    <li>Learn to hold a baby</li>
    <li>Set a feeding scdedule</li>
  </ul>

  <svg width="0" height="0" style="position:absolute">
    <defs>
      <symbol id="star" viewBox="0 0 20 20"><path d="M10 1l2.7 5.9 6.3.7-4.7 4.3 1.3 6.3L10 15l-5.6 3.2 1.3-6.3L1 7.6l6.3-.7z"/></symbol>
    </defs>
  </svg>

  <article class="product-card" style="left:418px; top:254px;">
    <div class="product-photo photo-a" role="img" aria-label="Photo of a smiling baby in a grey infant car seat"></div>
    <h2 class="product-title">Utenm adminim veniam, quis nostrud ex erctation ullamco laboris</h2>
    <div class="rating"><div class="stars"><svg><use href="#star"/></svg><svg><use href="#star"/></svg><svg><use href="#star"/></svg><svg><use href="#star"/></svg><svg><use href="#star"/></svg></div><span class="rating-count">678,67 ratings</span></div>
    <p class="product-text">I went out to buy my first car seat inand had earn my PhD in car seats, Newtonian physic s, and anti-stain technology</p>
  </article>

  <article class="product-card" style="left:759px; top:254px;">
    <div class="product-photo photo-b" role="img" aria-label="Photo of a mother buckling her baby into a car seat"></div>
    <h2 class="product-title">Utenm adminim veniam, quis nostrud ex erctation ullamco laboris</h2>
    <div class="rating"><div class="stars"><svg><use href="#star"/></svg><svg><use href="#star"/></svg><svg><use href="#star"/></svg><svg><use href="#star"/></svg><svg><use href="#star"/></svg></div><span class="rating-count">678,67 ratings</span></div>
    <p class="product-text">I went out to buy my first car seat inand had earn my PhD in car seats, Newtonian physic s, and anti-stain technology</p>
  </article>

  <article class="product-card" style="left:418px; top:676px;">
    <div class="product-photo photo-c" role="img" aria-label="Photo of a laughing toddler in a black car seat"></div>
    <h2 class="product-title">Utenm adminim veniam, quis nostrud ex erctation ullamco laboris</h2>
    <div class="rating"><div class="stars"><svg><use href="#star"/></svg><svg><use href="#star"/></svg><svg><use href="#star"/></svg><svg><use href="#star"/></svg><svg><use href="#star"/></svg></div><span class="rating-count">678,67 ratings</span></div>
    <p class="product-text">I went out to buy my first car seat inand had earn my PhD in car seats, Newtonian physic s, and anti-stain technology</p>
  </article>

  <article class="product-card" style="left:759px; top:676px;">
    <div class="product-photo photo-d" role="img" aria-label="Photo of a baby in a knit hat sitting in a car seat"></div>
    <h2 class="product-title">Utenm adminim veniam, quis nostrud ex erctation ullamco laboris</h2>
    <div class="rating"><div class="stars"><svg><use href="#star"/></svg><svg><use href="#star"/></svg><svg><use href="#star"/></svg><svg><use href="#star"/></svg><svg><use href="#star"/></svg></div><span class="rating-count">678,67 ratings</span></div>
    <p class="product-text">I went out to buy my first car seat inand had earn my PhD in car seats, Newtonian physic s, and anti-stain technology</p>
  </article>

  <footer class="site-footer">
    <p class="footer-links">Home | About | Products | Articles | Contact us</p>
    <p class="copyright">Copyrights 2013. All Rights Reserved.</p>
    <div class="social">
      <span style="background:var(--social-a)" aria-label="Social link"></span>
      <span style="background:var(--social-b)" aria-label="Social link"></span>
      <span style="background:var(--social-c)" aria-label="Feed link"></span>
      <span style="background:var(--social-d)" aria-label="Video link"></span>
    </div>
  </footer>
</body>
</html>
```